Social Media Graphics - Oakline Push REVISED

Create 6-7 individual social media graphics (square size) to encourage folks to join our online course called:

The Harvest Ledger Circle
How to Launch a Multi-Million Business From Scratch
Sign Up Today!

IMPORTANT: Make the largest and most prominent text on the graphic be: How to Launch a Multi-Million Business From Scratch

For the color scheme of the graphics, let's try a blue color palette; make sure the graphics appeal to both men and women

Make sure each graphic contains 1 of the 3 pics attached (crop pic as needed); and make sure one of the graphics is all TEXT only.

Target Market(s)

men and women looking to start a business

Industry/Entity Type

Entrepreneurship

Colors
0054AA
0677BA
7BADD7
CADEEF
E8F1F8

Requirements
Must have
• All the text and use the 3 pics provided; one graphic can be all text; Simple, modern design that's easy to read

```html
<!DOCTYPE html>
<html lang="en">
<head>
<meta charset="utf-8">
<title>The Harvest Ledger Circle – Sign Up</title>
<link rel="stylesheet" href="https://fonts.googleapis.com/css2?family=Exo+2:ital,wght@0,800;0,900;1,800;1,900&display=swap">
<style>
  :root {
    --brand-blue: #0677BA;
    --deep-blue: #0054AA;
    --title-blue: #1457B8;
    --sky: #7BADD7;
    --mist: #CADEEF;
    --ice: #E8F1F8;
    --ink: #111111;
    --pill-dark: #1C1C1C;
    --white: #FFFFFF;
    --silver-light: #F4F4F4;
    --silver-dark: #A9AEB3;
  }
  * { margin: 0; padding: 0; box-sizing: border-box; }
  html, body { width: 1200px; height: 1200px; overflow: hidden; }
  body { font-family: "Exo 2", sans-serif; }

  .graphic {
    position: relative;
    width: 1200px;
    height: 1200px;
    background: var(--brand-blue);
    overflow: hidden;
  }

  .hosts-photo {
    position: absolute;
    left: 233px;
    top: 83px;
    width: 790px;
    height: 600px;
    border-radius: 300px 300px 40px 40px;
    background: radial-gradient(ellipse at 35% 35%, #3a3f4a 0%, #23262d 45%, #1d4f86 80%, rgba(6,119,186,0) 100%);
  }

  .title-panel {
    position: absolute;
    left: 0;
    top: 0;
    width: 1200px;
    height: 1200px;
  }

  .title-block {
    position: absolute;
    left: 214px;
    top: 585px;
    width: 806px;
    text-align: center;
  }

  .title-line {
    display: flex;
    justify-content: center;
    align-items: center;
    gap: 12px;
    font-style: italic;
    font-weight: 900;
    text-transform: uppercase;
    color: var(--title-blue);
    line-height: 1;
  }
  .title-the { font-size: 38px; }
  .title-pill {
    font-size: 36px;
    color: var(--ice);
    background: var(--pill-dark);
    border-radius: 12px;
    padding: 6px 18px 8px;
  }
  .title-main {
    font-size: 46px;
    margin-top: 4px;
    letter-spacing: 1px;
  }

  .course-promise {
    margin-top: 16px;
    font-style: italic;
    font-weight: 900;
    font-size: 52px;
    line-height: 1.12;
    text-transform: uppercase;
    color: var(--ink);
  }

  .signup-button {
    position: absolute;
    left: 337px;
    top: 1047px;
    width: 524px;
    height: 104px;
    border-radius: 52px;
    background: linear-gradient(180deg, var(--silver-light) 0%, #DCDFE2 50%, var(--silver-dark) 100%);
    border: 5px solid #C7CBCF;
    box-shadow: 0 6px 12px rgba(0,0,0,0.35);
    display: flex;
    align-items: center;
    justify-content: center;
    font-style: italic;
    font-weight: 900;
    font-size: 48px;
    text-transform: uppercase;
    color: var(--ink);
  }
</style>
</head>
<body>
  <main class="graphic">
    <div class="hosts-photo" role="img" aria-label="Photo of the two course hosts, a man in a black turtleneck with arms crossed and a woman in a denim jacket, both smiling"></div>

    <svg class="title-panel" viewBox="0 0 1200 1200" aria-hidden="true">
      <path fill="var(--white)" d="M617,500 C600,540 560,560 500,565 L330,565 Q300,565 300,600 L300,615 Q300,645 260,645 Q214,645 214,690 L214,815 Q214,860 260,860 Q300,860 300,895 L300,930 Q300,960 340,960 L540,960 C580,965 605,990 617,1028 C629,990 654,965 694,960 L895,960 Q935,960 935,930 L935,895 Q935,860 975,860 Q1020,860 1020,815 L1020,690 Q1020,645 975,645 Q935,645 935,615 L935,600 Q935,565 905,565 L734,565 C674,560 634,540 617,500 Z"/>
    </svg>

    <div class="title-block">
      <h2>
        <span class="title-line"><span class="title-the">The</span><span class="title-pill">Harvest Ledger</span></span>
        <span class="title-line title-main">Circle</span>
      </h2>
      <h1 class="course-promise">How to Launch a<br>Multi-Million Business<br>From Scratch</h1>
    </div>

    <div class="signup-button">Sign Up Today!</div>
  </main>
</body>
</html>
```